Business Card - connecting 2 souls and beggining the journey of self discovery

Logo on the front
with tag line

On the back list of services and contact details

Seminars
workshops
Coaching
podcasts

Darren Whitlow
Health & Wellbeing Life Coach
0491 372 615
darren@brightcoreliving.example
brightcoreliving.example

Industry/Entity Type

Life Coaching

Contact Information for Business Card

I like the use of colour from the logo to be used. I'm not a fan of white.

Requirements
Must have
• My tagline: The way forward begins with you
Nice to have
• Use of colour that is in the mind body soul logo

```html
<!DOCTYPE html>
<html lang="en">
<head>
<meta charset="utf-8">
<title>Bright Core Living – Business Card</title>
<link rel="stylesheet" href="https://fonts.googleapis.com/css2?family=Montserrat:wght@500;600&family=Open+Sans:wght@400;600&display=swap">
<style>
  :root {
    --page-bg: #ecebe8;
    --card-green: #58b68f;
    --text-white: #ffffff;
    --badge-silver: #e4e4e6;
    --badge-edge: #c9c9cc;
    --badge-text: #3f8f6d;
  }
  * { margin: 0; padding: 0; box-sizing: border-box; }
  html, body {
    width: 1200px; height: 900px; overflow: hidden;
    background: var(--page-bg);
  }
  .card {
    position: absolute; left: 145px; top: 170px;
    width: 910px; height: 560px;
    background: var(--card-green);
    border-radius: 22px;
    color: var(--text-white);
    font-family: "Open Sans", sans-serif;
  }
  .brand-name {
    position: absolute; left: 28px; top: 52px;
    font-family: "Montserrat", sans-serif; font-weight: 500;
    font-size: 39px; letter-spacing: -0.5px; line-height: 1;
  }
  .tagline {
    position: absolute; left: 32px; top: 112px;
    font-family: "Open Sans", sans-serif; font-weight: 600;
    font-size: 18.5px; text-transform: uppercase; letter-spacing: 0.2px;
  }
  .person-name {
    position: absolute; left: 32px; top: 176px;
    font-family: "Montserrat", sans-serif; font-weight: 600;
    font-size: 30px; text-transform: uppercase; letter-spacing: 0.3px; line-height: 1;
  }
  .person-role {
    position: absolute; left: 32px; top: 218px;
    font-size: 21.5px;
  }
  .contact-list, .service-list {
    position: absolute; left: 32px; list-style: none;
    font-size: 22px; line-height: 33px;
  }
  .contact-list { top: 273px; }
  .service-list { top: 380px; }
  .contact-list li, .service-list li {
    display: flex; align-items: center; gap: 8px;
  }
  .contact-icon { width: 16px; height: 16px; flex: none; }
  .bullet {
    width: 16px; height: 16px; border-radius: 50%;
    background: var(--text-white); flex: none;
  }
  .brand-badge {
    position: absolute; left: 427px; top: 56px;
    width: 448px; height: 448px; border-radius: 50%;
    background: radial-gradient(circle at 40% 35%, #f6f6f7 0%, var(--badge-silver) 60%, var(--badge-edge) 100%);
    display: flex; align-items: center; justify-content: center;
  }
  .brand-badge-name {
    font-family: "Montserrat", sans-serif; font-weight: 600;
    font-size: 34px; color: var(--badge-text); text-align: center; line-height: 1.2;
  }
</style>
</head>
<body>
  <main class="card">
    <h1 class="brand-name">Bright Core Living</h1>
    <p class="tagline">The way forward begins with you</p>

    <h2 class="person-name">Darren Whitlow</h2>
    <p class="person-role">Health &amp; Wellbeing Life Coach</p>

    <ul class="contact-list">
      <li>
        <svg class="contact-icon" viewBox="0 0 16 16" aria-hidden="true"><path fill="#fff" d="M3.6 1.2l2.2 2.6-1.2 1.6c.9 2 2.4 3.5 4.4 4.4l1.6-1.2 2.6 2.2-1.2 2.6C6.9 13.6 2.4 9.1 1 3.9z"/></svg>
        0491 372 615
      </li>
      <li>
        <svg class="contact-icon" viewBox="0 0 16 16" aria-hidden="true"><rect x="1.5" y="3.5" width="13" height="9" rx="1" fill="#fff"/><path d="M2 4.2l6 4.4 6-4.4" fill="none" stroke="#58b68f" stroke-width="1.3"/></svg>
        darren@brightcoreliving.example
      </li>
      <li>
        <svg class="contact-icon" viewBox="0 0 16 16" aria-hidden="true"><circle cx="8" cy="8" r="6.8" fill="#fff"/><path d="M1.5 8h13M8 1.2c-2.4 2-2.4 11.6 0 13.6M8 1.2c2.4 2 2.4 11.6 0 13.6" fill="none" stroke="#58b68f" stroke-width="1.1"/></svg>
        www.brightcoreliving.example
      </li>
    </ul>

    <ul class="service-list">
      <li><span class="bullet"></span>Seminars</li>
      <li><span class="bullet"></span>Workshops</li>
      <li><span class="bullet"></span>Coaching</li>
      <li><span class="bullet"></span>Podcasts</li>
    </ul>

    <div class="brand-badge">
      <span class="brand-badge-name">Bright Core<br>Living</span>
    </div>
  </main>
</body>
</html>
```